Velmora Cabinets Letter Head and Email Signature

Hi
I would love a design package for a letterhead, email signature, even update my business card if you like if you can come up with a great idea for my new high end cabinet shop. Velmora Cabinets brings timeless craftsmanship to modern interiors, specializing in high end, custom cabinetry designed for architects and interior designers.

Target Market(s)

high end, luxury market

Industry/Entity Type

cabinet making

Requirements
Must have
• my colours of logo as the theme

```html
<!DOCTYPE html>
<html lang="en">
<head>
<meta charset="utf-8">
<title>Velmora Cabinets – Letterhead</title>
<link href="https://fonts.googleapis.com/css2?family=Montserrat:wght@400;500&family=Tinos&display=swap" rel="stylesheet">
<style>
  :root {
    --ink: #0a0a0a;
    --leaf: #4b7d4c;
    --paper: #ffffff;
    --backdrop: #b9b9b9;
    --body-text: #141414;
  }
  html, body {
    margin: 0;
    width: 1200px;
    height: 1159px;
    overflow: hidden;
    background: var(--backdrop);
  }
  .letterhead {
    position: absolute;
    left: 220px;
    top: 42px;
    width: 760px;
    height: 1075px;
    background: var(--paper);
    overflow: hidden;
    box-shadow: 0 6px 24px rgba(0,0,0,0.25);
    font-family: "Montserrat", Arial, sans-serif;
  }
  .letterhead__waves {
    position: absolute;
    inset: 0;
    width: 760px;
    height: 1075px;
  }
  .wave--ink { fill: var(--ink); }
  .wave--leaf { fill: var(--leaf); }

  .contact {
    position: absolute;
    top: 22px;
    right: 26px;
    list-style: none;
    margin: 0;
    padding: 0;
    font-family: "Tinos", "Times New Roman", serif;
    color: var(--paper);
    font-size: 14px;
    line-height: 19px;
    text-align: right;
  }
  .contact__item {
    display: flex;
    justify-content: flex-end;
    align-items: center;
    gap: 10px;
  }
  .contact__icon {
    width: 18px;
    height: 18px;
    flex: none;
  }
  .contact__icon circle { fill: var(--leaf); }
  .contact__icon path { fill: none; stroke: var(--paper); stroke-width: 1.4; stroke-linecap: round; stroke-linejoin: round; }
  .contact__indent { margin-right: 28px; }

  .brand-name {
    position: absolute;
    left: 60px;
    top: 238px;
    margin: 0;
    font-family: "Montserrat", Arial, sans-serif;
    font-weight: 500;
    font-size: 38px;
    line-height: 46px;
    letter-spacing: 1px;
    color: var(--leaf);
  }

  .letter-body {
    position: absolute;
    left: 110px;
    top: 340px;
    width: 560px;
    color: var(--body-text);
    font-size: 13px;
    line-height: 17px;
  }
  .letter-body p { margin: 0 0 36px; }
</style>
</head>
<body>
<main class="letterhead">
  <svg class="letterhead__waves" viewBox="0 0 760 1075" aria-hidden="true">
    <path class="wave--leaf" d="M0,0 H760 V152 C650,228 470,203 320,193 C180,185 60,163 0,133 Z"/>
    <path class="wave--ink" d="M0,0 H760 V140 C650,215 470,190 320,180 C180,172 60,150 0,120 Z"/>
    <path class="wave--leaf" d="M0,1075 V955 C180,880 480,925 760,760 V1075 Z"/>
    <path class="wave--ink" d="M0,1075 V975 C180,900 480,945 760,782 V1075 Z"/>
  </svg>

  <ul class="contact">
    <li class="contact__item">0491 570 156
      <svg class="contact__icon" viewBox="0 0 18 18"><circle cx="9" cy="9" r="9"/><path d="M6 5 l2 2 -1 1.5 q1 2 2.5 2.5 l1.5 -1 2 2 -1.5 1.5 q-4 0 -7 -5 z"/></svg>
    </li>
    <li class="contact__item">info@velmoracabinets.com.au
      <svg class="contact__icon" viewBox="0 0 18 18"><circle cx="9" cy="9" r="9"/><path d="M4.5 6 h9 v6 h-9 z M4.5 6 l4.5 3.5 4.5 -3.5"/></svg>
    </li>
    <li class="contact__item">www.websitename.com
      <svg class="contact__icon" viewBox="0 0 18 18"><circle cx="9" cy="9" r="9"/><path d="M9 4 a5 5 0 1 0 0.01 0 M4 9 h10 M9 4 q-3 5 0 10 q3 -5 0 -10"/></svg>
    </li>
    <li class="contact__item">421, Address line here
      <svg class="contact__icon" viewBox="0 0 18 18"><circle cx="9" cy="9" r="9"/><path d="M9 14 q-4 -4 -4 -6.5 a4 4 0 0 1 8 0 q0 2.5 -4 6.5 z M9 6.5 v1.5"/></svg>
    </li>
    <li class="contact__item contact__indent">Country Name, 45452</li>
  </ul>

  <h1 class="brand-name">Velmora Cabinets</h1>

  <section class="letter-body">
    <p>Lorem ipsum dolor sit amet, consectetur adipiscing elit. Donec fringilla neque euismod volutpat cursus. Vestibulum ac pretium orci, consequat elementum velit. Etiam bibendum purus ac augue finibus volutpat. Vestibulum justo nisl</p>
    <p>Lorem ipsum dolor sit amet, consectetur adipiscing elit. Donec fringilla neque euismod volutpat cursus. Vestibulum ac pretium orci, consequat elementum velit. Etiam bibendum purus ac augue finibus volutpat. Vestibulum justo nisl, gravida aliquet sollicitudin ut, finibus vitae mi. Praesent aliquet scelerisque blandit. Sed id varius lacus, id tristique sem. Fusce et lobortis leo. Aliquam mollis pellentesque magna, condimentum ullamcorper ex ullamcorper non. Morbi ultricies nunc eu tellus dignissim, eget venenatis dolor ullamcorper. Etiam dolor eros, iaculis at ultricies nec, volutpat nec orci. Vivamus tincidunt rutrum sapien, ac porttitor mauris tristique nec.</p>
    <p>Lorem ipsum dolor sit amet, consectetur adipiscing elit. Donec fringilla neque euismod volutpat cursus. Vestibulum ac pretium orci, consequat elementum velit. Etiam bibendum purus ac augue finibus volutpat. Vestibulum justo nisl, gravida aliquet sollicitudin ut, finibus vitae mi. Praesent aliquet scelerisque blandit. Sed id varius lacus, id tristique sem. Fusce et lobortis leo. Aliquam mollis pellentesque magna, condimentum ullamcorper ex ullamcorper non. Morbi ultricies nunc eu tellus dignissim, eget venenatis dolor ullamcorper. Etiam dolor eros, iaculis at ultricies nec, volutpat nec orci. Vivamus tincidunt rutrum sapien, ac porttitor mauris tristique nec.</p>
    <p>Lorem ipsum dolor sit amet, consectetur adipiscing elit. Donec fringilla neque euismod volutpat cursus. Vestibulum ac pretium orci, consequat elementum velit. Etiam bibendum purus ac augue finibus volutpat. Vestibulum justo nisl</p>
  </section>
</main>
</body>
</html>
```